sticker for cleaning products

it is in the bottle. products are bio-cleaner. Toilet Cleaner - yellow Sanitary Cleaner - orange Glass Cleaner - light blue All purpose cleaner - green Hand Soap - cream Detergent - olive Detergent - rose bottles is used RUNDA: https://glasbehalterwerk.de/katalog/#Runda shape of the sticker is not geometric. It's something like a cloud / leaf / drop / ?? the sticker has an inner space with only the product name and color. the sticker has an outer space. here we want to mark out "powered by KORVINEL" (our company name, find logo attached)

```html
<!DOCTYPE html>
<html lang="en">
<head>
<meta charset="utf-8">
<title>All Purpose Cleaner – Sticker</title>
<link rel="stylesheet" href="https://fonts.googleapis.com/css2?family=Bebas+Neue&family=Montserrat:wght@500;800&display=swap">
<style>
  :root {
    --leaf-deep: #3f9a3c;
    --leaf-light: #8fcb5e;
    --leaf-inner-deep: #47a443;
    --leaf-inner-light: #86c557;
    --leaf-rim: #2c6e2a;
    --banner: #ffffff;
    --shadow: #9a9a9a;
    --ink: #161616;
    --brand-ink: #3a3a3a;
    --brand-accent: #b38b69;
    --paper: #ffffff;
  }
  html, body {
    margin: 0;
    padding: 0;
    overflow: hidden;
    background: var(--paper);
  }
  .sticker {
    position: relative;
    width: 936px;
    height: 1200px;
    overflow: hidden;
    background: var(--paper);
  }
  .sticker__art {
    position: absolute;
    inset: 0;
  }
  .label-word {
    font-family: "Bebas Neue", "Arial Narrow", sans-serif;
    text-anchor: middle;
  }
  .label-word--top { font-size: 168px; fill: var(--ink); letter-spacing: 2px; }
  .label-word--main { font-size: 168px; fill: var(--ink); letter-spacing: 3px; }
  .label-word--bottom { font-size: 134px; fill: var(--paper); letter-spacing: 3px; }
  .credit {
    position: absolute;
    left: 0;
    top: 0;
    width: 936px;
    height: 1200px;
    font-family: "Montserrat", Arial, sans-serif;
  }
  .credit__lead {
    position: absolute;
    left: 269px;
    top: 950px;
    font-size: 18px;
    font-weight: 800;
    color: var(--ink);
  }
  .credit__mark {
    position: absolute;
    left: 402px;
    top: 908px;
    width: 102px;
    height: 102px;
    border-radius: 50%;
    border: 5px solid var(--brand-accent);
    box-sizing: border-box;
  }
  .credit__name {
    position: absolute;
    left: 0;
    width: 936px;
    top: 1018px;
    text-align: center;
    font-size: 36px;
    font-weight: 500;
    letter-spacing: 14px;
    text-indent: 14px;
    color: var(--brand-ink);
  }
</style>
</head>
<body>
<main class="sticker">
  <svg class="sticker__art" width="936" height="1200" viewBox="0 0 936 1200" aria-label="All Purpose Cleaner label">
    <defs>
      <linearGradient id="leaf-fill" x1="0" y1="0" x2="1" y2="0">
        <stop offset="0" stop-color="var(--leaf-deep)"/>
        <stop offset="1" stop-color="var(--leaf-light)"/>
      </linearGradient>
      <linearGradient id="leaf-inner-fill" x1="0" y1="0" x2="1" y2="0">
        <stop offset="0" stop-color="var(--leaf-inner-deep)"/>
        <stop offset="1" stop-color="var(--leaf-inner-light)"/>
      </linearGradient>
      <path id="leaf-shape" d="M800,40 C860,200 862,300 850,420 C838,620 690,792 468,792 C245,792 88,630 86,410 C84,190 250,22 480,18 C600,14 720,28 800,40 Z"/>
      <filter id="soft-shadow" x="-10%" y="-10%" width="120%" height="130%">
        <feDropShadow dx="0" dy="8" stdDeviation="6" flood-color="#000" flood-opacity="0.3"/>
      </filter>
    </defs>

    <polygon class="ribbon-tail" points="22,300 74,272 74,440" fill="var(--shadow)"/>
    <polygon class="ribbon-tail" points="914,300 862,272 862,440" fill="var(--shadow)"/>

    <use class="leaf-shadow" href="#leaf-shape" transform="translate(0 10)" fill="var(--shadow)"/>
    <use class="leaf" href="#leaf-shape" fill="url(#leaf-fill)"/>
    <use class="leaf-inner-rim" href="#leaf-shape" transform="translate(468 415) scale(0.82) translate(-468 -405)" fill="var(--leaf-rim)"/>
    <use class="leaf-inner" href="#leaf-shape" transform="translate(468 405) scale(0.82) translate(-468 -405)" fill="url(#leaf-inner-fill)"/>

    <rect class="banner" x="22" y="294" width="892" height="220" rx="10" fill="var(--banner)" filter="url(#soft-shadow)"/>

    <text class="label-word label-word--top" x="468" y="266">ALL</text>
    <text class="label-word label-word--main" x="468" y="464">PURPOSE</text>
    <text class="label-word label-word--bottom" x="468" y="632">CLEANER</text>
  </svg>

  <footer class="credit">
    <span class="credit__lead">powered by</span>
    <span class="credit__mark" aria-hidden="true"></span>
    <div class="credit__name">KORVINEL</div>
  </footer>
</main>
</body>
</html>
```